New Business Card Design Project LORVANTI-Italy

we are LORVANTI-Italy
our company in the market for 3 years we are luxury cosmetic company and its about time for a facelift :)
i will like to have elegant luxurious and unique business card
that will give the person that get it a unique, luxurious and elegant impression
I'm VERY OPEN FOR NEW IDEAS , even duo i add a few files of things that i see on line and i like them

i add my logo as well
my website is LORVANTI.COM
(if you would like to see the main style that we have)

Target Market(s)

adult that have money :)

Industry/Entity Type

Business

Contact Information for Business Card

Name - Dario Lorvanti
Position - CEO and CO Founder
address - 4817 E Halvern
telephone - 555-384-1926
email - dario@lorvanti.com
fax - 555-384-1926
website - LORVANTI.COM

Colors
000000
959595
fbee3e
ffffff

Requirements
Must have
• big logo in GOLD color
• elegant look
• impressive
Nice to have
• not must but maybe classy pattern background
• not must but maybe emblem
• maybe clear plastic business card
Should not have
• colors
• images

```html
<!DOCTYPE html>
<html lang="en">
<head>
<meta charset="utf-8">
<title>LORVANTI Italy – Business Card</title>
<link href="https://fonts.googleapis.com/css2?family=Tinos:wght@400;700&family=PT+Sans:wght@400;700&display=swap" rel="stylesheet">
<style>
  :root {
    --backdrop: #3f3f3f;
    --card-dark: #161616;
    --card-mid: #222222;
    --gold: #d6a832;
    --gold-soft: #b8912a;
    --text-light: #e6e6e6;
  }
  * { margin: 0; padding: 0; box-sizing: border-box; }
  html, body {
    width: 1200px; height: 900px; overflow: hidden;
    background: var(--backdrop);
  }
  .canvas { position: relative; width: 1200px; height: 900px; }

  .card {
    position: absolute; top: 170px; width: 348px; height: 562px;
    background:
      repeating-linear-gradient(90deg, rgba(255,255,255,0.018) 0 1px, transparent 1px 3px),
      linear-gradient(160deg, var(--card-mid), var(--card-dark));
    text-align: center;
  }
  .card--front { left: 260px; }
  .card--back  { left: 632px; }

  .brand-mark {
    position: absolute; left: 50%; transform: translateX(-50%);
    border: 3px solid var(--gold); border-radius: 50%;
    display: flex; align-items: center; justify-content: center;
  }
  .card--front .brand-mark { top: 43px; width: 210px; height: 210px; }
  .card--back .brand-mark  { top: 158px; width: 124px; height: 124px; }

  .brand-name {
    font-family: "Tinos", "Times New Roman", serif;
    font-weight: 400; color: var(--gold); letter-spacing: 1px;
  }
  .card--front .brand-name { font-size: 30px; }

  .holder {
    position: absolute; top: 326px; left: 0; right: 0;
  }
  .holder__name {
    font-family: "Tinos", "Times New Roman", serif; font-weight: 700;
    font-size: 21px; color: var(--gold); letter-spacing: 0.5px;
  }
  .holder__role {
    font-family: "PT Sans", Arial, sans-serif; font-size: 14.5px;
    color: var(--text-light); margin-top: 1px;
  }
  .divider {
    position: absolute; top: 390px; left: 90px; width: 166px; height: 1px;
    background: var(--gold-soft);
  }
  .contacts {
    position: absolute; top: 413px; left: 0; right: 0;
    font-family: "PT Sans", Arial, sans-serif; font-size: 14.5px;
    line-height: 20.5px; color: var(--text-light);
  }
  .contacts b { color: var(--gold); font-weight: 700; }
  .contacts .web { color: var(--gold); }
  .contacts .address { margin-top: 17px; }

  .wordmark {
    position: absolute; top: 306px; left: 0; right: 0;
    font-size: 54px; line-height: 60px; letter-spacing: 1px;
  }
  .wordmark-rule {
    position: absolute; top: 373px; left: 32px; width: 282px; height: 2px;
    background: var(--gold);
  }
  .origin {
    position: absolute; top: 384px; left: 0; right: 0;
    font-family: "Tinos", "Times New Roman", serif;
    font-size: 21px; color: var(--gold); letter-spacing: 1px;
  }
</style>
</head>
<body>
<main class="canvas">
  <section class="card card--front" aria-label="Card front">
    <div class="brand-mark"><span class="brand-name">LORVANTI</span></div>
    <div class="holder">
      <p class="holder__name">DARIO LORVANTI</p>
      <p class="holder__role">CEO and CO Founder</p>
    </div>
    <div class="divider"></div>
    <div class="contacts">
      <p><b>P:</b> 555-384-1926</p>
      <p><b>F:</b> 555-384-1926</p>
      <p><b>E:</b> dario@lorvanti.com</p>
      <p class="web">www.lorvanti.com</p>
      <p class="address">4817 E Halvern</p>
    </div>
  </section>

  <section class="card card--back" aria-label="Card back">
    <div class="brand-mark"></div>
    <p class="wordmark brand-name">LORVANTI</p>
    <div class="wordmark-rule"></div>
    <p class="origin">ITALY</p>
  </section>
</main>
</body>
</html>
```